Realtor branding business card

modern, simple and self branding. Broker office logo needs to be used but not emphasized. Looking to brand myself

Target Market(s)

buyers, sellers and investors

Industry/Entity Type

Realtor

Contact Information for Business Card

Sample of my current business card on file

Requirements
Must have
• my website - tobiasmerrowkl.com
• Realtor logo
• Fair housing logo
Nice to have
• Colors from office logo but not a must
Should not have
• Do not want headshot

```html
<!DOCTYPE html>
<html lang="en">
<head>
<meta charset="utf-8">
<title>Tobias Merrow – Realtor Business Card</title>
<link rel="stylesheet" href="https://fonts.googleapis.com/css2?family=Montserrat:wght@400;500;700;800&display=swap">
<style>
  :root {
    --stage: #2b2b2b;
    --brand-red: #d82628;
    --brand-navy: #272a78;
    --card-white: #ffffff;
    --text-gray: #5a5a5a;
    --badge-gray: #9a9aa6;
  }
  * { box-sizing: border-box; margin: 0; padding: 0; }
  html, body {
    width: 1200px; height: 780px; overflow: hidden;
    background: var(--stage);
    font-family: "Montserrat", Arial, sans-serif;
  }
  .canvas { position: relative; width: 1200px; height: 780px; }
  .card {
    position: absolute; width: 580px; height: 331px;
    box-shadow: 0 14px 30px rgba(0,0,0,.45);
  }
  .card-front {
    left: 80px; top: 70px;
    background: var(--brand-red); color: var(--card-white);
  }
  .card-back {
    left: 530px; top: 360px;
    background: var(--card-white);
  }
  .brand-mark {
    display: flex; align-items: center; gap: 10px;
    font-weight: 700; line-height: 1.1;
  }
  .brand-mark .mark-square { width: 14px; height: 14px; flex: none; }
  .card-front .brand-mark {
    position: absolute; left: 0; right: 0; top: 122px; justify-content: center;
    font-size: 24px;
  }
  .card-front .mark-square { background: var(--card-white); }
  .front-web {
    position: absolute; left: 0; right: 0; bottom: 34px;
    text-align: center; font-size: 14px; letter-spacing: .3px;
  }
  .card-back .brand-mark {
    position: absolute; left: 52px; top: 140px; width: 250px;
    color: var(--brand-navy); font-size: 20px;
  }
  .card-back .mark-square { background: var(--brand-red); }
  .divider {
    position: absolute; left: 310px; top: 62px; width: 2px; height: 200px;
    background: var(--brand-red);
  }
  .contact { position: absolute; left: 334px; top: 56px; width: 236px; color: var(--text-gray); }
  .agent-name { color: var(--brand-navy); font-weight: 800; font-size: 24px; letter-spacing: .3px; line-height: 1.1; }
  .agent-title { font-size: 13px; margin: 3px 0 12px; }
  .contact-list { list-style: none; font-size: 13.5px; line-height: 19px; }
  .contact-list li { display: flex; align-items: center; gap: 9px; white-space: nowrap; }
  .contact-list svg { width: 11px; height: 11px; flex: none; }
  .address { font-size: 13.5px; line-height: 19px; margin-top: 12px; }
  .badges {
    position: absolute; right: 22px; bottom: 18px;
    display: flex; align-items: center; gap: 10px;
  }
  .badge { width: 26px; height: 26px; background: var(--badge-gray); }
  .badge-round { border-radius: 50%; }
</style>
</head>
<body>
<main class="canvas">
  <section class="card card-front" aria-label="Business card front">
    <div class="brand-mark"><span class="mark-square"></span><span>Brightmark<br>Realty Group</span></div>
    <p class="front-web">www.tobiasmerrowkl.com</p>
  </section>

  <section class="card card-back" aria-label="Business card back">
    <div class="brand-mark"><span class="mark-square"></span><span>Brightmark<br>Realty Group</span></div>
    <div class="divider"></div>
    <div class="contact">
      <h1 class="agent-name">TOBIAS MERROW</h1>
      <p class="agent-title">Realtor</p>
      <ul class="contact-list">
        <li><svg viewBox="0 0 12 12" aria-hidden="true"><rect x="3" y="0.5" width="6" height="11" rx="1" fill="none" stroke="#272a78" stroke-width="1.2"/><circle cx="6" cy="9.5" r=".7" fill="#272a78"/></svg>407. 555. 0143</li>
        <li><svg viewBox="0 0 12 12" aria-hidden="true"><path d="M2.5 1 L4.5 1 L5.2 3.6 L4 4.6 Q5 7 7.4 8 L8.4 6.8 L11 7.5 L11 9.5 Q10.5 11 9 11 Q1 10 1 2.5 Q1 1 2.5 1 Z" fill="#272a78"/></svg>407. 555. 0188</li>
        <li><svg viewBox="0 0 12 12" aria-hidden="true"><rect x="0.6" y="2.2" width="10.8" height="7.6" fill="none" stroke="#272a78" stroke-width="1.2"/><path d="M.8 2.6 L6 6.6 L11.2 2.6" fill="none" stroke="#272a78" stroke-width="1.2"/></svg>info@tobiasmerrowkl.com</li>
        <li><svg viewBox="0 0 12 12" aria-hidden="true"><circle cx="6" cy="6" r="5.2" fill="none" stroke="#272a78" stroke-width="1.1"/><ellipse cx="6" cy="6" rx="2.3" ry="5.2" fill="none" stroke="#272a78" stroke-width="1"/><path d="M.8 6 H11.2" stroke="#272a78" stroke-width="1"/></svg>www.tobiasmerrowkl.com</li>
      </ul>
      <p class="address">482 Larkspur Avenue<br>Cedar Hollow, FL 32790</p>
    </div>
    <div class="badges">
      <span class="badge" role="img" aria-label="Realtor association badge"></span>
      <span class="badge badge-round" role="img" aria-label="Equal housing opportunity badge"></span>
    </div>
  </section>
</main>
</body>
</html>
```